Business card design needed

I would like a one sided black business card with the information provided above. Refer to my website www.brightvolleyracquets.com.au for an example of colors I have used for my site, would like to keep this consistent for my business cards also, I will upload my logo below.

I am a new small business that provides tennis customers with racquet re stringing, tennis strings and accessories.

Industry/Entity Type

Small Business

Contact Information for Business Card

Bright Volley Tennis

Owen Whitby
Managing Director

brightvolleyracquets@mailbox.example
www.brightvolleyracquets.com.au
0491 726 305

Racquet Restringing/Tennis Strings/Accessories

Requirements
Must have
• Must have my logo and card must be black

```html
<!DOCTYPE html>
<html lang="en">
<head>
<meta charset="utf-8">
<title>Bright Volley Tennis – Business Card</title>
<link rel="stylesheet" href="https://fonts.googleapis.com/css2?family=Source+Sans+3:ital,wght@0,400;0,700;1,700&display=swap">
<style>
  :root {
    --page-bg: #e8e5e0;
    --card-black: #040606;
    --lime: #b6d334;
    --volley-blue: #1e5a95;
    --white: #ffffff;
    --ink: #111111;
  }
  html, body {
    margin: 0;
    width: 1200px;
    height: 750px;
    overflow: hidden;
    background: var(--page-bg);
    font-family: "Source Sans 3", "Myriad Pro", Arial, sans-serif;
  }
  .business-card {
    position: absolute;
    left: 75px;
    top: 75px;
    width: 1050px;
    height: 597px;
    border-radius: 32px;
    overflow: hidden;
    background: var(--card-black);
    box-shadow: 0 6px 18px rgba(0,0,0,0.25);
  }
  .card-waves {
    position: absolute;
    inset: 0;
    width: 1050px;
    height: 597px;
  }
  .wave-green { fill: var(--lime); }
  .wave-edge { fill: var(--card-black); }
  .wave-blue { fill: var(--volley-blue); }
  .wave-body { fill: var(--card-black); }

  .holder {
    position: absolute;
    right: 57px;
    top: 62px;
    text-align: right;
    color: var(--ink);
  }
  .holder-name {
    margin: 0;
    font-size: 33px;
    font-weight: 700;
    line-height: 1.1;
  }
  .holder-title {
    margin: 10px 0 0;
    font-size: 25px;
    font-weight: 400;
  }

  .brand {
    position: absolute;
    left: 52px;
    top: 262px;
    display: flex;
    align-items: center;
    gap: 16px;
  }
  .brand-dot {
    width: 40px;
    height: 40px;
    border-radius: 50%;
    background: var(--lime);
  }
  .brand-name {
    margin: 0;
    font-size: 50px;
    font-weight: 700;
    color: var(--lime);
    letter-spacing: 0.5px;
  }

  .services {
    position: absolute;
    left: 52px;
    top: 458px;
    margin: 0;
    padding: 0;
    list-style: none;
    color: var(--white);
    font-size: 25px;
    line-height: 35px;
  }
  .services li::before {
    content: "";
    display: inline-block;
    width: 8px;
    height: 8px;
    background: var(--white);
    margin-right: 10px;
    vertical-align: middle;
    position: relative;
    top: -3px;
  }

  .contact {
    position: absolute;
    right: 58px;
    top: 443px;
    margin: 0;
    text-align: right;
    color: var(--white);
    font-size: 25px;
    line-height: 43px;
  }
  .contact-label {
    font-weight: 700;
    font-style: italic;
  }
</style>
</head>
<body>
  <div class="business-card">
    <svg class="card-waves" viewBox="0 0 1050 597" aria-hidden="true">
      <rect class="wave-green" x="0" y="0" width="1050" height="597"/>
      <path class="wave-edge" d="M0,88 C300,38 500,188 760,183 C900,180 1000,172 1050,160 L1050,597 L0,597 Z"/>
      <path class="wave-blue" d="M0,98 C300,52 500,198 760,193 C900,190 1000,178 1050,164 L1050,597 L0,597 Z"/>
      <path class="wave-body" d="M0,142 C260,95 500,212 760,206 C900,203 1000,190 1050,170 L1050,597 L0,597 Z"/>
    </svg>

    <div class="holder">
      <p class="holder-name">Owen Whitby</p>
      <p class="holder-title">Managing Director</p>
    </div>

    <div class="brand">
      <span class="brand-dot"></span>
      <p class="brand-name">Bright Volley Tennis</p>
    </div>

    <ul class="services">
      <li>Racquet Restringing</li>
      <li>Tennis Strings</li>
      <li>Accessories</li>
    </ul>

    <p class="contact">
      <span class="contact-label">phone</span> 0491 726 305<br>
      <span class="contact-label">email</span> brightvolleyracquets@mailbox.example<br>
      <span class="contact-label">web</span> www.brightvolleyracquets.com.au
    </p>
  </div>
</body>
</html>
```